Accountancy firm needs clean and simple website and optional logo

We need a logo and basic wordpress website design for a Sydney based accountancy firm.
We need a clean and simple logo and website, based on the accounting/finance/tax industry. Simple, credible and official colors.
The logo is expected to be so simple that we have combined into the one job.
If you submit a logo design and we choose it along with someone else's website design you will be paid a bonus of $60. The website design will still win the competition as per normal.
Current website is old and terrible but gives you an idea of the sitemap (super simple) and what they do: www.brookfiscal.com.au
We want original different to normal template looking designs.
We like videos, and like http://www.merivane.com.au/
Feel free to go to clipvault9 and use some videos from there.
We are based in Sydney Australia and in the field of taxation and accounting
We want a clean, formal, credible site, limited pages.
The project is guaranteed, so go for it.
Logo Text
Brook & Associates

```html
<!DOCTYPE html>
<html lang="en">
<head>
<meta charset="utf-8">
<title>Brook &amp; Associates — Tax Accountants</title>
<link rel="stylesheet" href="https://fonts.googleapis.com/css2?family=Open+Sans:wght@400;600;700&family=Ubuntu:wght@400;500&display=swap">
<style>
  :root {
    --brand-blue: #1f9ad8;
    --ink: #3a3a3a;
    --muted: #8a8a8a;
    --paper: #ffffff;
    --footer: #2c2c2c;
    --footer-base: #1e1e1e;
    --footer-text: #bdbdbd;
    --hero-top: #0d1a3a;
    --hero-mid: #2b3d78;
    --hero-low: #3a2a4c;
  }
  * { box-sizing: border-box; margin: 0; padding: 0; }
  html, body { width: 887px; height: 1200px; overflow: hidden; }
  body { font-family: "Open Sans", Arial, sans-serif; color: var(--ink); background: var(--paper); position: relative; }

  .site-header { position: absolute; top: 0; left: 0; width: 887px; height: 88px; background: var(--paper); }
  .brand-name { position: absolute; left: 74px; top: 24px; font-family: "Open Sans", Arial, sans-serif; font-weight: 400; font-size: 22px; color: var(--ink); letter-spacing: .2px; }
  .call-us { position: absolute; right: 74px; top: 26px; font-size: 15px; color: var(--brand-blue); font-family: "Ubuntu", sans-serif; }
  .main-nav { position: absolute; right: 74px; top: 58px; display: flex; gap: 24px; }
  .main-nav a { font-size: 11px; color: #333; text-decoration: none; text-transform: uppercase; letter-spacing: .4px; }
  .main-nav a.active { color: var(--brand-blue); }

  .hero { position: absolute; top: 88px; left: 0; width: 887px; height: 356px; }
  .hero-photo { position: absolute; inset: 0; background: linear-gradient(180deg, var(--hero-top) 0%, var(--hero-mid) 45%, var(--hero-low) 70%, #120e1c 100%); }
  .hero-copy { position: absolute; left: 74px; top: 116px; color: #fff; width: 260px; }
  .hero-title { font-family: "Ubuntu", sans-serif; font-weight: 400; font-size: 25px; letter-spacing: .5px; }
  .hero-text { font-size: 9px; line-height: 1.5; margin-top: 6px; color: #dfe4f2; }
  .btn { display: inline-block; background: var(--brand-blue); color: #fff; font-size: 9px; padding: 6px 14px; text-decoration: none; }
  .hero-copy .btn { margin-top: 14px; }
  .hero-arrow { position: absolute; top: 176px; width: 18px; height: 22px; background: rgba(0,0,0,.55); }
  .hero-arrow.prev { left: 0; }
  .hero-arrow.next { right: 0; }
  .hero-arrow svg { display: block; margin: 6px auto; }

  .section-title { font-family: "Ubuntu", sans-serif; font-weight: 400; font-size: 25px; text-align: center; color: #2a2a2a; letter-spacing: .5px; }
  .about { position: absolute; top: 462px; left: 0; width: 887px; text-align: center; }
  .about-text { width: 740px; margin: 10px auto 0; font-size: 9.5px; line-height: 1.55; color: var(--muted); }
  .about .btn { margin-top: 14px; }

  .services-title { position: absolute; top: 600px; left: 0; width: 887px; }
  .services { position: absolute; top: 662px; left: 74px; width: 739px; display: flex; gap: 15px; }
  .service { width: 236px; }
  .service-photo { width: 236px; height: 126px; }
  .photo-desk { background: linear-gradient(135deg, #dfe3e8, #9aa6b4); }
  .photo-charts { background: linear-gradient(135deg, #cfd8e2, #6f8aa6); }
  .photo-meeting { background: linear-gradient(135deg, #e6e3de, #5a6270); }
  .service-name { font-family: "Ubuntu", sans-serif; font-weight: 400; font-size: 21px; color: var(--brand-blue); margin-top: 16px; text-transform: uppercase; }
  .service-text { font-size: 9px; line-height: 1.5; color: var(--muted); margin-top: 4px; height: 40px; }
  .service-link { display: inline-block; margin-top: 8px; font-size: 9px; color: var(--brand-blue); text-decoration: none; }

  .site-footer { position: absolute; top: 912px; left: 0; width: 887px; height: 248px; background: var(--footer); color: var(--footer-text); }
  .footer-col { position: absolute; top: 28px; }
  .footer-heading { font-family: "Ubuntu", sans-serif; font-weight: 400; font-size: 15px; color: #e8e8e8; text-transform: uppercase; letter-spacing: .4px; margin-bottom: 16px; }
  .footer-col p, .footer-col li { font-size: 8.5px; line-height: 1.7; }
  .footer-col ul { list-style: none; }
  .col-contact { left: 74px; width: 250px; }
  .col-contact .spacer { height: 10px; }
  .col-legal { left: 349px; }
  .col-news { left: 488px; width: 200px; }
  .email-field { margin-top: 14px; width: 128px; height: 26px; background: #fff; color: #777; font-size: 8px; padding: 7px 8px; }
  .col-news .btn { margin-top: 10px; }
  .col-social { left: 754px; }
  .social-item { display: flex; align-items: center; gap: 7px; font-size: 8.5px; margin-bottom: 7px; }
  .social-dot { width: 11px; height: 11px; background: var(--brand-blue); }
  .footer-base { position: absolute; top: 1160px; left: 0; width: 887px; height: 40px; background: var(--footer-base); color: #8d8d8d; font-size: 8px; text-align: center; line-height: 40px; }
</style>
</head>
<body>
  <header class="site-header">
    <div class="brand-name">Brook &amp; Associates</div>
    <div class="call-us">Call us: 02 9000 4172</div>
    <nav class="main-nav">
      <a class="active" href="#">Home</a>
      <a href="#">About Us</a>
      <a href="#">Services</a>
      <a href="#">Contact Us</a>
    </nav>
  </header>

  <section class="hero">
    <div class="hero-photo" role="img" aria-label="Night view of Sydney Harbour with the bridge and city lights reflected in the water"></div>
    <div class="hero-copy">
      <h1 class="hero-title">ACCOUNTING</h1>
      <p class="hero-text">Tax planning and lodgement for individuals and small businesses across Sydney.</p>
      <a class="btn" href="#">Read More</a>
    </div>
    <span class="hero-arrow prev"><svg width="6" height="10" viewBox="0 0 6 10"><path d="M5 1 1 5l4 4" fill="none" stroke="#fff" stroke-width="1.5"/></svg></span>
    <span class="hero-arrow next"><svg width="6" height="10" viewBox="0 0 6 10"><path d="M1 1l4 4-4 4" fill="none" stroke="#fff" stroke-width="1.5"/></svg></span>
  </section>

  <section class="about">
    <h2 class="section-title">ABOUT US</h2>
    <p class="about-text">We help Sydney households and businesses keep their finances in order, with clear advice on tax, bookkeeping and planning. Our team has served local clients for many years and takes pride in careful, personal service. We work with sole traders, families and growing companies, and we explain every figure in plain language so you always know where you stand.</p>
    <a class="btn" href="#">Read More</a>
  </section>

  <h2 class="section-title services-title">OUR SERVICES</h2>
  <section class="services">
    <article class="service">
      <div class="service-photo photo-desk" role="img" aria-label="Desk with financial papers, calculator and pen"></div>
      <h3 class="service-name">Accounting</h3>
      <p class="service-text">Clear monthly accounts and reports that show how your business is tracking, prepared on time and explained in plain terms.</p>
      <a class="service-link" href="#">Read More</a>
    </article>
    <article class="service">
      <div class="service-photo photo-charts" role="img" aria-label="Financial charts and graphs on paper"></div>
      <h3 class="service-name">Finance</h3>
      <p class="service-text">Practical help with budgets, loans and cash flow so you can plan ahead and make confident decisions for your future.</p>
      <a class="service-link" href="#">Read More</a>
    </article>
    <article class="service">
      <div class="service-photo photo-meeting" role="img" aria-label="Advisers meeting with a client over documents"></div>
      <h3 class="service-name">Tax Preparation</h3>
      <p class="service-text">Returns for individuals, trusts and companies, lodged accurately with every deduction you are entitled to claim this year.</p>
      <a class="service-link" href="#">Read More</a>
    </article>
  </section>

  <footer class="site-footer">
    <div class="footer-col col-contact">
      <h4 class="footer-heading">Contact Us</h4>
      <p>Visit our office or call us to book a meeting with our team.</p>
      <div class="spacer"></div>
      <p>(02) 9000 4172</p>
      <p>info@brookfiscal.com.au</p>
    </div>
    <div class="footer-col col-legal">
      <h4 class="footer-heading">Legal</h4>
      <ul>
        <li>Terms of Service</li>
        <li>Privacy Policy</li>
        <li>Regulation</li>
      </ul>
    </div>
    <div class="footer-col col-news">
      <h4 class="footer-heading">Newsletter</h4>
      <p>Sign up to get news and tax updates sent to your inbox each month.</p>
      <div class="email-field">Enter Your Email</div>
      <a class="btn" href="#">Subscribe</a>
    </div>
    <div class="footer-col col-social">
      <h4 class="footer-heading">Social</h4>
      <div class="social-item"><span class="social-dot"></span>Facefeed</div>
      <div class="social-item"><span class="social-dot"></span>Chirper</div>
      <div class="social-item"><span class="social-dot"></span>RSS</div>
    </div>
  </footer>
  <div class="footer-base">©2015 brookfiscal.com.au. All rights reserved</div>
</body>
</html>
```